Design a Website in Wordpress for an Australian Health Training Company in Health related courses

We require a WORDPRESS based Website (due to add on's we need to use for third party software) to replace our old site.
We offer national face to face delivery in medical reception, terminology and also administration.
The website will have around 6 pages and the ability to describe our main 6 courses (perhaps on the Courses page this may be tabs opening up to details for example?)
I have attached a previous sample of a Joomla site which was being developed (please do not feel you have to copy this - but I am just giving it as a sample - copying would be boring). But it gives an idea of look/feel and colours which may be suitable. Open to other ideas though.
I will provide some of the content, but would like the ability to finish the content myself.
Images and graphics are important. While a few medical photos re great - don't be tempted to us all pictures of doctors and nurses (although a couple would be good) - these are administrative courses so general corporate, eye catching visionary pictures of people in general are great. A medical type picture is also fine.
THE BOOKING system - will be via an ADD ON which will occur at the end of the project and is supplied by a third party software company (our student management system). This project will include up to 2 hours working with the Tech guys from the third party software to enable the ADD ON. If this ADD ON requires more time, we will pay hourly (although I do not expect it will).
Target Market(s)
Mostly a female market, many mature aged women target 25-45 yrs. Mixture of medical/health and corporate. Maybe a bit of mums returning to work and corporate inspiration.
Industry/Entity Type
It Company
Coding
Coded - Design and coding required
Number of Pages Required
5+ page
Requirements
Must have
- Wordpress
- Great graphics
- Interesting
- professional and clean
- Enquiry section (info Pak)
- Should have a University feel to it - Education
- Pages
- Home Page - About Us - Recruitment -Courses - Class Schedule - Traineeships Queensland Funding - Latest News Blog - Corporate Training- Contact us

```html
<!DOCTYPE html>
<html lang="en">
<head>
<meta charset="utf-8">
<title>Kestrel Institute of Training</title>
<link href="https://fonts.googleapis.com/css2?family=Cinzel:wght@400;600;700&family=Open+Sans:wght@400;600;700&display=swap" rel="stylesheet">
<style>
:root{
  --blue:#0b4ea2;
  --blue-deep:#083f87;
  --blue-text:#1a4f9c;
  --orange:#f7a234;
  --cyan:#0aa3d6;
  --grey-bar:#ececec;
  --grey-text:#6b6b6b;
  --card-hi:#ebebeb;
  --footer:#232323;
  --white:#ffffff;
}
*{margin:0;padding:0;box-sizing:border-box}
html,body{width:1200px;height:2546px;overflow:hidden}
body{font-family:"Open Sans",Arial,sans-serif;color:#333;background:var(--white);position:relative}
.serif{font-family:"Cinzel",Georgia,serif}
.btn{display:inline-block;background:var(--orange);color:var(--white);font-weight:700;font-size:11px;text-transform:uppercase;letter-spacing:.3px}

/* top bar */
.topbar{position:absolute;top:0;left:0;width:1200px;height:31px;background:var(--grey-bar);font-size:12px;color:#555}
.topbar .contact{position:absolute;top:8px;display:flex;align-items:center;gap:8px}
.topbar .socials{position:absolute;right:135px;top:11px;display:flex;gap:9px}
.topbar .socials span{width:8px;height:8px;border-radius:50%;background:#5a86c4}

/* header */
.header{position:absolute;top:31px;left:0;width:1200px;height:144px;background:var(--white)}
.brand{position:absolute;left:136px;top:22px;width:130px;text-align:center;color:var(--blue-deep);font-family:"Cinzel",Georgia,serif;font-weight:700;font-size:13px;line-height:15px}
.brand .mark{width:46px;height:46px;border:0;border-radius:50%;background:var(--blue-deep);margin:8px auto 0}
.nav{position:absolute;left:311px;top:71px;display:flex;align-items:center;font-size:12.5px;color:var(--blue-text)}
.nav a{color:var(--blue-text);text-decoration:none;padding:4px 7px}
.nav a.active{background:var(--blue);color:var(--white);border-radius:2px}
.nav .sep{color:#8aa4c8;font-size:11px}

/* hero */
.hero{position:absolute;top:175px;left:0;width:1200px;height:427px;background:linear-gradient(100deg,#6d5a4e 0%,#a68b78 25%,#c9bfb6 55%,#e6e4e2 75%,#b7a497 100%)}
.hero-caption{position:absolute;left:143px;top:108px;width:405px;height:206px;background:var(--blue);color:var(--white);text-align:center;padding:26px 22px}
.hero-caption h1{font-family:"Cinzel",Georgia,serif;font-size:27px;font-weight:700;margin-bottom:12px}
.hero-caption p{font-size:12.5px;line-height:20px;margin-bottom:14px}
.hero-caption .btn{padding:8px 13px}
.dots{position:absolute;display:flex;gap:8px}
.dots span{width:13px;height:13px;border-radius:50%;background:#333;border:2px solid #333}
.dots span.on{background:#ddd}
.wave{position:absolute;left:0;top:545px;width:1200px;height:60px}

/* intro band */
.intro{position:absolute;top:600px;left:0;width:1200px;height:285px;background:var(--blue);color:var(--white);text-align:center}
.intro h2{font-family:"Cinzel",Georgia,serif;font-size:22px;font-weight:700;margin-top:52px}
.intro p{width:1015px;margin:18px auto 0;font-size:10.5px;line-height:19.5px}
.intro .btn{margin-top:14px;padding:8px 13px}

/* courses */
.courses{position:absolute;top:885px;left:0;width:1200px;height:360px}
.courses h2{font-family:"Cinzel",Georgia,serif;text-align:center;color:var(--blue);font-size:21px;font-weight:700;margin-top:17px}
.course-grid{position:absolute;left:132px;top:65px;display:flex}
.course{width:156px;height:251px;border-right:1px solid #e1e1e1;text-align:center;padding-top:26px}
.course:last-child{border-right:0}
.course.featured{background:var(--card-hi)}
.course svg{width:40px;height:40px}
.course h3{font-family:"Cinzel",Georgia,serif;font-weight:400;color:#8c8c8c;font-size:14px;line-height:19px;margin:8px 10px 0;height:58px}
.course p{font-size:11px;line-height:16px;color:#333;margin:6px 12px 0}
.course .btn{margin-top:10px;padding:6px 9px;font-size:9.5px}

/* enquiry + why */
.panel{position:absolute;top:1244px;left:0;width:1200px;height:611px;background:linear-gradient(90deg,#1d57a6 0%,#2a63ad 45%,#1b56a5 100%);color:var(--white)}
.enquiry{position:absolute;left:173px;top:30px;width:332px}
.panel h2{font-family:"Cinzel",Georgia,serif;font-size:21px;font-weight:600}
.enquiry .sub{color:var(--orange);font-family:"Cinzel",Georgia,serif;font-size:13px;margin:6px 0 22px 5px}
.field{height:39px;background:var(--white);color:#444;font-size:12px;padding:12px 16px;margin-bottom:16px}
.submit{position:absolute;right:0;padding:9px 16px;font-size:12px}
.why{position:absolute;left:581px;top:30px;width:480px}
.why-item{position:relative;padding-left:60px;margin-top:26px}
.why-item svg{position:absolute;left:0;top:2px;width:36px;height:30px}
.why-item h3{font-family:"Cinzel",Georgia,serif;font-size:15px;font-weight:600}
.why-item p{font-size:11.5px;line-height:19px;margin-top:6px}

/* testimonials */
.testimonials{position:absolute;top:1855px;left:0;width:1200px;height:390px;background:linear-gradient(90deg,#f4f6f8 0%,#eef1f4 50%,#dfe6ed 100%)}
.testimonials .photo{position:absolute;left:628px;top:0;width:572px;height:390px;background:linear-gradient(120deg,#e8edf2 0%,#c9b39a 30%,#d9c7b3 55%,#b9cde2 80%,#e4ecf4 100%)}
.testimonials h2{position:absolute;left:190px;top:44px;font-family:"Cinzel",Georgia,serif;color:var(--blue);font-size:22px;font-weight:600}
.testimonials blockquote{position:absolute;left:190px;top:89px;width:425px;font-size:14px;line-height:27px;color:#444;text-align:justify}
.testimonials .name{position:absolute;left:195px;top:279px;font-family:"Cinzel",Georgia,serif;color:var(--blue);font-size:28px;font-weight:700}

/* tweet bar */
.tweet{position:absolute;top:2223px;left:132px;width:935px;height:60px;background:var(--cyan);color:var(--white);font-size:11.5px;line-height:16px}
.tweet .dot{position:absolute;left:82px;top:20px;width:20px;height:20px;border-radius:50%;background:var(--white)}
.tweet p{position:absolute;left:162px;top:13px;width:640px}

/* footer */
.footer{position:absolute;top:2283px;left:0;width:1200px;height:263px;background:var(--footer);color:#ddd}
.footer h4{font-family:"Cinzel",Georgia,serif;font-weight:400;font-size:20px;color:var(--white);letter-spacing:.5px}
.f-links{position:absolute;left:170px;top:38px}
.f-links .cols{display:flex;gap:30px;margin:14px 0 0 15px}
.f-links ul{list-style:none;font-size:12px;line-height:19px}
.f-links li::before{content":: ";color:#aaa}
.f-links li::before{content:":: ";color:#aaa}
.f-contact{position:absolute;left:540px;top:38px}
.f-contact .row{display:flex;gap:12px;font-size:12.5px;line-height:19px;margin-top:12px}
.f-contact .row:first-of-type{margin-top:14px}
.f-contact svg{width:12px;height:14px;flex:none;margin-top:3px}
.f-news{position:absolute;left:811px;top:38px}
.f-news .input{margin-top:13px;width:217px;height:32px;border:1px solid #888;font-size:11px;padding:8px 10px;position:relative}
.f-news .input svg{position:absolute;right:10px;top:10px;width:11px;height:11px}
.f-news .social{display:flex;gap:10px;margin-top:14px}
.f-news .social span{width:31px;height:31px}
.copyright{position:absolute;top:228px;width:1200px;text-align:center;font-size:9.5px;color:#999}
</style>
</head>
<body>

<div class="topbar">
  <div class="contact" style="left:132px">
    <svg width="14" height="14" viewBox="0 0 14 14"><path d="M3 1l3 3-2 2c1 2 2 3 4 4l2-2 3 3-2 2C6 13 1 8 1 3z" fill="none" stroke="#1a4f9c" stroke-width="1.2"/></svg>
    <span>+0400 555 210</span>
  </div>
  <div class="contact" style="left:268px">
    <svg width="16" height="12" viewBox="0 0 16 12"><rect x="1" y="1" width="14" height="10" fill="none" stroke="#1a4f9c" stroke-width="1.2"/><path d="M1 1l7 6 7-6" fill="none" stroke="#1a4f9c" stroke-width="1.2"/></svg>
    <span>hello@kestrelinstitute.example</span>
  </div>
  <div class="socials"><span></span><span></span><span></span><span></span><span></span><span></span><span></span><span></span></div>
</div>

<header class="header">
  <div class="brand">Kestrel Institute<br>of Training<div class="mark"></div></div>
  <nav class="nav">
    <a class="active">Home</a><span class="sep">::</span>
    <a>About Us</a><span class="sep">::</span>
    <a>Recruitment</a><span class="sep">::</span>
    <a>Courses</a><span class="sep">::</span>
    <a>Class Schedule</a><span class="sep">::</span>
    <a>TQF</a><span class="sep">::</span>
    <a>Latest News Blog</a><span class="sep">::</span>
    <a>Corporate Training</a><span class="sep">::</span>
    <a>Contact us</a>
  </nav>
</header>

<section class="hero" role="img" aria-label="Photo of a trainer presenting at a whiteboard to a seated class in a brick-walled classroom">
  <div class="hero-caption">
    <h1>Welcome To Our Website</h1>
    <p>Kestrel is Australia's Leading Provider of Educational, Training and Support Services for the Medical and Dental industry – enabling students to be immediately skilled and 'Job Ready' for a career in Health.</p>
    <span class="btn">Read More</span>
  </div>
</section>
<svg class="wave" viewBox="0 0 1200 60" preserveAspectRatio="none"><path d="M0 18 C300 60 700 58 1200 0 L1200 60 L0 60 Z" fill="#0b4ea2"/></svg>
<div class="dots" style="left:561px;top:582px"><span></span><span class="on"></span><span></span><span></span></div>

<section class="intro">
  <h2>Welcome to Kestrel Institute of Training</h2>
  <p>Kestrel is a Registered Training Organisation offering specialised Medical Administration Training in over 15 locations Australia wide. Kestrel have trained thousands of students the required knowledge and skills to become successful health care administrators. Our unique Short Medical Reception and Terminology Course and our Full Qualification is Nationally Accredited and the go-to recognised qualification in industry. Did you know that Kestrel has been operating in Australia for over 16 years! During this time, Kestrel have developed a reputation second to none for training highly sought after medical receptionists, secretaries and administrators. Our course material and unique training programme is developed in conjunction with Industry to reflect the latest requirements in health administration. Kestrel also believe understanding the medical culture is as important as good skills. Our team of specialised trainers are both experienced in industry and also hold special qualifications in adult education and are fully accredited.</p>
  <span class="btn">Read More</span>
</section>

<section class="courses">
  <h2>List of Courses</h2>
  <div class="course-grid">
    <div class="course featured">
      <svg viewBox="0 0 40 40"><circle cx="15" cy="11" r="6" fill="#f39c2b"/><path d="M4 32c0-8 5-12 11-12s11 4 11 12z" fill="#f39c2b"/><rect x="22" y="22" width="16" height="12" fill="#f39c2b"/></svg>
      <h3>Medical Reception &amp; Terminology</h3>
      <p>Ad nisi adipiscing interdum erat ullamcorper vivamus a sodales dui.Id aptent a parturient ut.</p>
      <span class="btn">Read More</span>
    </div>
    <div class="course">
      <svg viewBox="0 0 40 40" fill="#8c8c8c"><circle cx="10" cy="13" r="4.5"/><circle cx="20" cy="10" r="5.5"/><circle cx="30" cy="13" r="4.5"/><path d="M2 32c0-7 4-11 8-11s8 4 8 11z"/><path d="M11 32c0-9 4-14 9-14s9 5 9 14z"/><path d="M22 32c0-7 4-11 8-11s8 4 8 11z"/></svg>
      <h3>Cert III Business Administration</h3>
      <p>Ad nisi adipiscing interdum erat ullamcorper vivamus a sodales dui.Id aptent a parturient ut.</p>
      <span class="btn">Read More</span>
    </div>
    <div class="course">
      <svg viewBox="0 0 40 40" fill="none" stroke="#8c8c8c" stroke-width="2.5"><circle cx="20" cy="11" r="6"/><path d="M8 36c0-9 5-14 12-14s12 5 12 14z"/><path d="M17 23v6h6v-6"/></svg>
      <h3>Medical Terminology</h3>
      <p>Ad nisi adipiscing interdum erat ullamcorper vivamus a sodales dui.Id aptent a parturient ut.</p>
      <span class="btn">Read More</span>
    </div>
    <div class="course">
      <svg viewBox="0 0 40 40" fill="none" stroke="#8c8c8c" stroke-width="2"><rect x="3" y="11" width="34" height="18" rx="2"/><path d="M8 16h2M13 16h2M18 16h2M23 16h2M28 16h2M8 20h2M13 20h2M18 20h2M23 20h2M28 20h2M12 24h16"/></svg>
      <h3>Keyboard and Typing</h3>
      <p>Ad nisi adipiscing interdum erat ullamcorper vivamus a sodales dui.Id aptent a parturient ut.</p>
      <span class="btn">Read More</span>
    </div>
    <div class="course">
      <svg viewBox="0 0 40 40"><circle cx="20" cy="20" r="14" fill="#8c8c8c"/><path d="M13 13c4 1 5 4 3 7s1 5 3 7M24 9c-1 4 2 5 5 6" fill="none" stroke="#fff" stroke-width="2"/></svg>
      <h3>Kestrel Online</h3>
      <p>Ad nisi adipiscing interdum erat ullamcorper vivamus a sodales dui.Id aptent a parturient ut.</p>
      <span class="btn">Read More</span>
    </div>
    <div class="course">
      <svg viewBox="0 0 40 40"><path d="M14 18v-6a6 6 0 0 1 12 0" fill="none" stroke="#8c8c8c" stroke-width="3"/><rect x="10" y="18" width="20" height="16" rx="2" fill="#8c8c8c"/></svg>
      <h3>Confidentiality</h3>
      <p>Ad nisi adipiscing interdum erat ullamcorper vivamus a sodales dui.Id aptent a parturient ut.</p>
      <span class="btn">Read More</span>
    </div>
  </div>
</section>

<section class="panel">
  <div class="enquiry">
    <h2>Request an Enquiry</h2>
    <div class="sub">Email Us</div>
    <div class="field">NAME</div>
    <div class="field">EMAIL</div>
    <div class="field">COURSE</div>
    <div class="field">STATE</div>
    <div class="field">MOBILE</div>
    <span class="btn submit">Submit</span>
  </div>
  <div class="why">
    <h2>Why Kestrel Institute ?</h2>
    <div class="why-item">
      <svg viewBox="0 0 36 30" fill="none" stroke="#fff" stroke-width="2"><path d="M8 3h20l6 8-16 17L2 11z M2 11h32 M14 3l-3 8 7 17 7-17-3-8"/></svg>
      <h3>Quality</h3>
      <p>Kestrel delivery quality, effective training facilitated by industry leaders. Just ask our students who rate us on average of 4.7 out of 5.</p>
    </div>
    <div class="why-item">
      <svg viewBox="0 0 36 30" fill="none" stroke="#fff" stroke-width="2.2"><path d="M4 13h6v15H4z M10 14l6-11c3 0 4 2 3 6l-1 4h9c2 0 3 2 2 4l-3 9c-1 2-2 2-4 2H10"/></svg>
      <h3>Experience</h3>
      <p>Kestrel is Australia's largest and leading providers of nationally recognised training in health administration – training from over 17 locations Australia wide.</p>
    </div>
    <div class="why-item">
      <svg viewBox="0 0 36 30"><path d="M18 2l4.5 9 10 1.4-7.2 7 1.7 10L18 24.8 9 29.4l1.7-10-7.2-7 10-1.4z" fill="#fff"/></svg>
      <h3>Value</h3>
      <p>Our innovative teaching approach allows us to deliver exceptional training at affordable prices with no hidden extras.</p>
    </div>
    <div class="why-item">
      <svg viewBox="0 0 36 30"><rect x="10" y="1" width="16" height="28" fill="#fff"/><g fill="#1d57a6"><rect x="13" y="5" width="3" height="3"/><rect x="20" y="5" width="3" height="3"/><rect x="13" y="11" width="3" height="3"/><rect x="20" y="11" width="3" height="3"/><rect x="13" y="17" width="3" height="3"/><rect x="20" y="17" width="3" height="3"/><rect x="16" y="23" width="4" height="6"/></g></svg>
      <h3>Industry Recognised</h3>
      <p>Kestrel work hand in hand with industry to develop our core programme and consolidate the programme annually to keep the programme fresh and relevant.</p>
    </div>
    <div class="why-item">
      <svg viewBox="0 0 36 30"><path d="M3 2v26h31" fill="none" stroke="#fff" stroke-width="2.2"/><g fill="#fff"><rect x="8" y="16" width="4" height="10"/><rect x="14" y="10" width="4" height="16"/><rect x="20" y="13" width="4" height="13"/><rect x="26" y="6" width="4" height="20"/></g></svg>
      <h3>Great Job Results</h3>
      <p>Kestrel students get jobs! Our focus is to create job-ready students who are mentored to achieve their goals. Kestrel also provide a recruitment service for industry and graduates.</p>
    </div>
  </div>
</section>

<section class="testimonials">
  <div class="photo" role="img" aria-label="Photo of a relaxed, smiling young man in a checked shirt leaning back at his desk"></div>
  <h2>Testimonials</h2>
  <blockquote>I completed the course on Feb 13th. Loved it. The trainers, Lena and Joy were excellent in their delivery and knowledge. I want to say a huge thank you for the course and knowledge I came away with. I have secured a fantastic job after my first application! Such good value for money too! I would highly recommend it. I'm a mature age person so it's never too late to up -skill yourself to get what you deserve!</blockquote>
  <div class="name">Mara Quinn</div>
  <div class="dots" style="left:197px;top:337px"><span></span><span class="on"></span><span></span><span></span></div>
</section>

<div class="tweet">
  <span class="dot"></span>
  <p>Mauris parturient a vestibulum metus at dui vestibulum laoreet parturient phasellus vestibulum in parturient adipiscing dignissim justo lorem feugiat.</p>
</div>

<footer class="footer">
  <div class="f-links">
    <h4>Quick Links</h4>
    <div class="cols">
      <ul><li>Home</li><li>About Us</li><li>Recruitment</li><li>Courses</li><li>Class Schedule</li></ul>
      <ul style="margin-left:110px"><li>TQF</li><li>Latest News Blog</li><li>Corporate Training</li><li>Contact us</li></ul>
    </div>
  </div>
  <div class="f-contact">
    <h4>Quick Links</h4>
    <div class="row"><svg viewBox="0 0 12 14"><path d="M6 13C2 8 1 6 1 5a5 5 0 0 1 10 0c0 1-1 3-5 8z" fill="none" stroke="#ddd" stroke-width="1.3"/><circle cx="6" cy="5" r="1.6" fill="#ddd"/></svg><span>Suite 4, 210 Harbour Road<br>Northbank</span></div>
    <div class="row"><svg viewBox="0 0 12 14"><path d="M2 1l3 3-1.5 1.5c.8 1.6 1.8 2.7 3.5 3.5L8.5 7.5l3 3L10 12C5 12 1 7 1 2z" fill="#ddd"/></svg><span>(02) 5550 1847</span></div>
    <div class="row"><svg viewBox="0 0 12 14"><rect x="1" y="4" width="10" height="7" fill="#ddd"/><path d="M1 4l5 4 5-4" fill="none" stroke="#232323"/></svg><span>info@kestrelinstitute.example</span></div>
  </div>
  <div class="f-news">
    <h4>Newsletter</h4>
    <div class="input">Enter Email id<svg viewBox="0 0 11 11"><path d="M1 5l9-4-4 9-1-4z" fill="#ddd"/></svg></div>
    <div class="social"><span style="background:#1b6fd1"></span><span style="background:#1da9e6"></span><span style="background:#d91f2a"></span><span style="background:#e22424"></span></div>
  </div>
  <div class="copyright">All Rights Reserved. Copyrights @ 2016 company name</div>
</footer>

</body>
</html>
```